Home Fund Guide

Have clients check their mortgage qualifications before they go looking for a mortgage lender. This program gains access to your lenders credit report / 3 scores without impacting your credit scores.

```html
<!DOCTYPE html>
<html lang="en">
<head>
<meta charset="utf-8">
<title>Home Fund Guide — Business Card</title>
<link href="https://fonts.googleapis.com/css2?family=Roboto:wght@400;500&display=swap" rel="stylesheet">
<style>
  :root {
    --page-bg: #d9d4cc;
    --card-bg: #eceef0;
    --brand-blue: #1b2f94;
    --panel-blue: #2640ad;
    --panel-blue-dark: #1e3497;
    --panel-blue-light: #2d4bbd;
    --brand-green: #1f9a4b;
    --leaf-green: #3cc456;
    --leaf-green-dark: #22974a;
    --name-light: #f1eef0;
    --text-dark: #1d1f24;
  }
  html, body {
    margin: 0;
    padding: 0;
    width: 1200px;
    height: 969px;
    overflow: hidden;
    background: var(--page-bg);
  }
  .card {
    position: absolute;
    left: 100px;
    top: 199px;
    width: 1000px;
    height: 571px;
    border-radius: 22px;
    background: var(--card-bg);
    overflow: hidden;
    font-family: "Roboto", Arial, sans-serif;
    box-shadow: 0 2px 10px rgba(0,0,0,0.12);
  }
  .hero-cards {
    position: absolute;
    left: 0;
    top: 34px;
    width: 420px;
    height: 140px;
    border-top-right-radius: 26px;
    background: linear-gradient(100deg, var(--leaf-green-dark) 0%, var(--leaf-green) 100%);
  }
  .identity-band {
    position: absolute;
    left: 0;
    top: 171px;
    width: 479px;
    height: 400px;
    border-top-right-radius: 30px;
    background: linear-gradient(160deg, var(--panel-blue-light) 0%, var(--panel-blue) 55%, var(--panel-blue-dark) 100%);
  }
  .person-name {
    position: absolute;
    left: 107px;
    top: 288px;
    margin: 0;
    font-size: 32px;
    font-weight: 500;
    color: var(--name-light);
    letter-spacing: 0.2px;
  }
  .person-role {
    position: absolute;
    left: 108px;
    top: 328px;
    margin: 0;
    font-size: 21px;
    font-weight: 400;
    color: var(--brand-green);
  }
  .brand-square {
    position: absolute;
    left: 736px;
    top: 82px;
    width: 104px;
    height: 104px;
    border-radius: 10px;
    background: var(--brand-blue);
  }
  .brand-name {
    position: absolute;
    right: 72px;
    top: 210px;
    margin: 0;
    font-size: 46px;
    font-weight: 500;
    color: var(--brand-blue);
    letter-spacing: -0.5px;
  }
  .contact-list {
    position: absolute;
    left: 0;
    top: 0;
    width: 100%;
    height: 100%;
    margin: 0;
    padding: 0;
    list-style: none;
  }
  .contact-line {
    position: absolute;
    right: 111px;
    font-size: 22px;
    line-height: 26px;
    color: var(--text-dark);
    white-space: nowrap;
    text-align: right;
  }
  .contact-icon {
    position: absolute;
    left: 905px;
    width: 18px;
    height: 18px;
    fill: var(--brand-green);
  }
</style>
</head>
<body>
  <main class="card">
    <div class="hero-cards" role="img" aria-label="Green stacked cards artwork"></div>
    <section class="identity-band" role="img" aria-label="Blue wallet artwork with rising arrow">
      <h2 class="person-name">Daniel Reyes</h2>
      <p class="person-role">President</p>
    </section>

    <div class="brand-square" aria-hidden="true"></div>
    <h1 class="brand-name">Home Fund Guide</h1>

    <ul class="contact-list">
      <li class="contact-line" style="top:308px">4120 Willowbend Road</li>
      <li class="contact-line" style="top:336px">Juneau, Alaska 99801</li>
      <li class="contact-line" style="top:373px">555-214-0386</li>
      <li class="contact-line" style="top:402px">555-318-7702</li>
      <li class="contact-line" style="top:430px">555-406-9125</li>
      <li class="contact-line" style="top:459px">info@homefundguide.com</li>
      <li class="contact-line" style="top:487px">homefundguide.com</li>
    </ul>

    <svg class="contact-icon" style="top:312px" viewBox="0 0 24 24" aria-label="Address">
      <path d="M12 1a8 8 0 0 0-8 8c0 6 8 14 8 14s8-8 8-14a8 8 0 0 0-8-8zm0 11a3 3 0 1 1 0-6 3 3 0 0 1 0 6z"/>
    </svg>
    <svg class="contact-icon" style="top:377px" viewBox="0 0 24 24" aria-label="Phone">
      <path d="M6.6 10.8a15 15 0 0 0 6.6 6.6l2.2-2.2a1 1 0 0 1 1-.25 11.4 11.4 0 0 0 3.6.57 1 1 0 0 1 1 1V20a1 1 0 0 1-1 1A17 17 0 0 1 3 4a1 1 0 0 1 1-1h3.5a1 1 0 0 1 1 1c0 1.250.2 2.450.57 3.6a1 1 0 0 1-.25 1z"/>
    </svg>
    <svg class="contact-icon" style="top:406px" viewBox="0 0 24 24" aria-label="Mobile">
      <path d="M7 1h10a2 2 0 0 1 2 2v18a2 2 0 0 1-2 2H7a2 2 0 0 1-2-2V3a2 2 0 0 1 2-2zm0 3v15h10V4z"/>
    </svg>
    <svg class="contact-icon" style="top:434px" viewBox="0 0 24 24" aria-label="Fax">
      <path d="M7 2h8l3 3v5H7zM3 11h18a2 2 0 0 1 2 2v8H1v-8a2 2 0 0 1 2-2zm2 4v2h4v-2z"/>
    </svg>
    <svg class="contact-icon" style="top:463px" viewBox="0 0 24 24" aria-label="Email">
      <path d="M2 5h20v14H2zm2 2v.5l8 5 8-5V7z"/>
    </svg>
    <svg class="contact-icon" style="top:491px" viewBox="0 0 24 24" aria-label="Website">
      <path d="M12 2a10 10 0 1 0 0 20 10 10 0 0 0 0-20zm-1 17.9A8 8 0 0 1 4.2 10.6L9 15v1a2 2 0 0 0 2 2zm6.9-2.5A2 2 0 0 0 16 16h-1v-3a1 1 0 0 0-1-1H8v-2h2a1 1 0 0 0 1-1V7h2a2 2 0 0 0 2-2v-.4a8 8 0 0 1 2.9 12.8z"/>
    </svg>
  </main>
</body>
</html>
```